New Company Business Card design

Looking for a corporate looking business card utilising my new logo design - the logo i would like embossed as one option and flat as another - simplistic but stylish - less is more - we are an import export business launching into the market - i would like a couple of options as main background - Grey or Black

```html
<!DOCTYPE html>
<html lang="en">
<head>
<meta charset="utf-8">
<title>Calder Trade Solutions – Business Cards</title>
<link rel="stylesheet" href="https://fonts.googleapis.com/css2?family=Crimson+Text:wght@400;600&display=swap">
<style>
  :root {
    --page: #ffffff;
    --charcoal: #333333;
    --slate: #6d6e71;
    --mid-grey: #666666;
    --silver: #d9d9d9;
    --brand-blue: #1274bc;
    --white: #ffffff;
    --ink: #1f1f1f;
  }
  html, body {
    margin: 0;
    padding: 0;
    width: 1200px;
    height: 1200px;
    overflow: hidden;
    background: var(--page);
  }
  .sheet {
    position: relative;
    width: 1200px;
    height: 1200px;
  }
  .card {
    position: absolute;
    width: 570px;
    height: 340px;
    border-radius: 16px;
    overflow: hidden;
  }
  .card svg { display: block; width: 570px; height: 340px; }
  .card--front-dark { left: 21px; top: 91px; background: var(--charcoal); }
  .card--back-dark  { left: 606px; top: 91px; background: var(--charcoal); }
  .card--front-light { left: 21px; top: 680px; background: var(--silver); }
  .card--back-light  { left: 606px; top: 680px; background: var(--silver); }

  .brand-name, .contact, .holder, .slogan {
    font-family: "Crimson Text", Georgia, serif;
  }
  .brand-name { font-size: 30px; font-weight: 600; fill: var(--brand-blue); letter-spacing: 0.5px; }
  .contact { font-size: 18px; text-anchor: end; }
  .holder { font-size: 23px; }
  .slogan { font-size: 24px; text-anchor: middle; }

  .on-dark { fill: var(--white); }
  .on-light { fill: var(--ink); }
</style>
</head>
<body>
<main class="sheet">

  <!-- Dark front -->
  <section class="card card--front-dark">
    <svg viewBox="0 0 570 340" aria-label="Front of business card, black version">
      <polygon fill="var(--brand-blue)" points="59,0 379,0 367,94"/>
      <polygon fill="var(--mid-grey)" points="379,0 546,0 375,45"/>
      <g class="brand">
        <circle cx="104" cy="150" r="9" fill="var(--brand-blue)"/>
        <text class="brand-name" x="122" y="140">Calder Trade</text>
        <text class="brand-name" x="122" y="174">Solutions</text>
      </g>
      <g class="contacts">
        <text class="contact on-dark" x="501" y="71">++ 555 014</text>
        <text class="contact on-dark" x="501" y="121">++ 555 027</text>
        <text class="contact on-dark" x="484" y="161">caldertrade.com</text>
        <text class="contact on-dark" x="501" y="205">hello@caldertrade.com</text>
        <g class="icon-phone"><rect x="516" y="48" width="20" height="40" rx="3" fill="var(--brand-blue)"/><rect x="519" y="54" width="14" height="28" fill="var(--mid-grey)"/></g>
        <g class="icon-handset"><circle cx="526" cy="120" r="11" fill="none" stroke="var(--brand-blue)" stroke-width="2"/><path d="M521 114 q-1 8 9 12 l2-3 -3-2 -2 2 q-4-2 -5-6 l2-1 -1-3z" fill="var(--brand-blue)"/></g>
        <g class="icon-home"><polygon points="512,158 526,144 540,158" fill="var(--brand-blue)"/><rect x="515" y="156" width="22" height="14" fill="var(--brand-blue)"/><rect x="523" y="161" width="6" height="9" fill="var(--charcoal)"/></g>
        <g class="icon-mail"><rect x="513" y="197" width="26" height="17" fill="var(--brand-blue)"/><polyline points="513,197 526,208 539,197" fill="none" stroke="var(--charcoal)" stroke-width="1.5"/></g>
      </g>
      <rect x="0" y="258" width="570" height="82" fill="var(--brand-blue)"/>
      <text class="holder on-dark" x="54" y="308">Mr. Daren Holt, Director</text>
    </svg>
  </section>

  <!-- Dark back -->
  <section class="card card--back-dark">
    <svg viewBox="0 0 570 340" aria-label="Back of business card, black version">
      <polygon fill="var(--brand-blue)" points="50,0 370,0 450,47"/>
      <polygon fill="var(--mid-grey)" points="370,0 532,0 418,29"/>
      <g class="brand">
        <circle cx="225" cy="150" r="9" fill="var(--brand-blue)"/>
        <text class="brand-name" x="243" y="140">Calder Trade</text>
        <text class="brand-name" x="243" y="174">Solutions</text>
      </g>
      <text class="slogan on-dark" x="285" y="287">Import Export Business Launching</text>
    </svg>
  </section>

  <!-- Grey front -->
  <section class="card card--front-light">
    <svg viewBox="0 0 570 340" aria-label="Front of business card, grey version">
      <polygon fill="var(--slate)" points="59,0 379,0 357,114"/>
      <polygon fill="var(--brand-blue)" points="379,0 546,0 372,49"/>
      <g class="brand">
        <circle cx="104" cy="150" r="9" fill="var(--brand-blue)"/>
        <text class="brand-name" x="122" y="140">Calder Trade</text>
        <text class="brand-name" x="122" y="174">Solutions</text>
      </g>
      <g class="contacts">
        <text class="contact on-light" x="501" y="71">++ 555 014</text>
        <text class="contact on-light" x="501" y="121">++ 555 027</text>
        <text class="contact on-light" x="484" y="161">caldertrade.com</text>
        <text class="contact on-light" x="501" y="205">hello@caldertrade.com</text>
        <g class="icon-phone"><rect x="516" y="48" width="20" height="40" rx="3" fill="none" stroke="var(--slate)" stroke-width="2"/></g>
        <g class="icon-handset"><circle cx="526" cy="120" r="11" fill="none" stroke="var(--slate)" stroke-width="2"/><path d="M521 114 q-1 8 9 12 l2-3 -3-2 -2 2 q-4-2 -5-6 l2-1 -1-3z" fill="var(--slate)"/></g>
        <g class="icon-home"><polygon points="512,158 526,144 540,158" fill="var(--slate)"/><rect x="515" y="156" width="22" height="14" fill="var(--slate)"/><rect x="523" y="161" width="6" height="9" fill="var(--silver)"/></g>
        <g class="icon-mail"><rect x="513" y="197" width="26" height="17" fill="var(--slate)"/><polyline points="513,197 526,208 539,197" fill="none" stroke="var(--silver)" stroke-width="1.5"/></g>
      </g>
      <rect x="0" y="258" width="570" height="82" fill="var(--slate)"/>
      <text class="holder on-dark" x="54" y="308">Mr. Daren Holt, Director</text>
    </svg>
  </section>

  <!-- Grey back -->
  <section class="card card--back-light">
    <svg viewBox="0 0 570 340" aria-label="Back of business card, grey version">
      <polygon fill="var(--brand-blue)" points="50,0 370,0 450,47"/>
      <polygon fill="var(--mid-grey)" points="370,0 532,0 418,29"/>
      <g class="brand">
        <circle cx="225" cy="150" r="9" fill="var(--brand-blue)"/>
        <text class="brand-name" x="243" y="140">Calder Trade</text>
        <text class="brand-name" x="243" y="174">Solutions</text>
      </g>
      <text class="slogan on-light" x="285" y="287">Import Export Business Launching</text>
    </svg>
  </section>

</main>
</body>
</html>
```